Life Coaching business needs a new flyer

We are an Australian business that specialises in Life Coaching, Career Coaching, Health and Wellness Coaching, Yoga and Pilates. We need a A4 double sided flyer that is full colour and folded to DL format. I have attached a couple of designs that I like and some pictures and would like the flyer to be bright yet stylish.

Industry/Entity Type

Life Coaching

```html
<!DOCTYPE html>
<html lang="en">
<head>
<meta charset="utf-8">
<title>Life Coaching and Meditation Centre of Excellence – DL Flyer</title>
<link rel="stylesheet" href="https://fonts.googleapis.com/css2?family=Source+Sans+3:ital,wght@0,400;0,600;0,700;1,700&display=swap">
<style>
  :root{
    --paper:#ffffff;
    --sky-light:#f2f8fc;
    --sky-mid:#d6eaf6;
    --green:#5aae2e;
    --blue:#1c74b9;
    --text:#6b6d70;
    --text-dark:#4d4f52;
    --trim:#9a9a9a;
    --photo-grass:#7a9a4a;
  }
  *{margin:0;padding:0;box-sizing:border-box}
  html,body{width:1200px;height:901px;overflow:hidden;background:var(--paper)}
  .sheet{
    position:absolute;left:0;top:0;width:968px;height:727px;
    transform:scale(1.23967);transform-origin:0 0;
    font-family:"Source Sans 3",sans-serif;color:var(--text);
  }
  .artwork{position:absolute;left:0;top:0;width:968px;height:727px}
  .block{position:absolute}
  .block h2{font-size:12.5px;font-weight:700;color:var(--blue);line-height:1.15;margin-bottom:2px}
  .block p{font-size:9.4px;line-height:1.32}
  .justify p{text-align:justify}
  .questions{left:75px;top:78px;width:245px}
  .ticks{list-style:none}
  .ticks li{position:relative;padding-left:13px;font-size:9.4px;line-height:1.3;margin-bottom:4px;color:var(--text-dark)}
  .ticks li::before{
    content:"";position:absolute;left:0;top:2.5px;width:8px;height:8px;border-radius:50%;background:var(--green);
  }
  .ticks li::after{
    content:"";position:absolute;left:2px;top:4.8px;width:2.6px;height:2.6px;
    border-top:1.2px solid #fff;border-right:1.2px solid #fff;transform:rotate(45deg);
  }
  .answer{left:75px;top:166px;font-size:12.5px;font-weight:700;font-style:italic;color:var(--green)}
  .services{left:356px;top:184px;width:252px}
  .services h2{margin-top:6px}
  .services h2:first-child{margin-top:0}
  .why{left:636px;top:76px;width:256px}
  .why h2{color:var(--green);font-size:13px}
  .why p{margin-bottom:3px}
  .why .ticks{margin-top:3px}
  .why .ticks li{color:var(--text);margin-bottom:1.5px;line-height:1.3}
  .about{left:75px;top:532px;width:258px}
  .about h2{margin-bottom:5px}
  .about p{color:var(--text-dark);line-height:1.38}
  .practice{left:638px;top:541px;width:252px}
  .practice h2{margin-top:6px}
  .practice h2:first-child{margin-top:0}
  .brand{
    position:absolute;left:231px;top:428px;width:78px;height:78px;border-radius:50%;
    display:flex;align-items:center;justify-content:center;text-align:center;
    font-size:11px;font-weight:700;line-height:1.1;color:var(--blue);
  }
</style>
</head>
<body>
<div class="sheet">
  <svg class="artwork" viewBox="0 0 968 727" xmlns="http://www.w3.org/2000/svg">
    <defs>
      <linearGradient id="paperTint" x1="0" y1="0" x2="0" y2="1">
        <stop offset="0" stop-color="var(--sky-light)"/>
        <stop offset="1" stop-color="var(--sky-mid)"/>
      </linearGradient>
      <linearGradient id="seaTone" x1="0" y1="0" x2="0" y2="1">
        <stop offset="0" stop-color="#5d9fd2"/>
        <stop offset="0.6" stop-color="#8cc0e3"/>
        <stop offset="1" stop-color="#3f7fb8"/>
      </linearGradient>
      <linearGradient id="skyTone" x1="0" y1="0" x2="0" y2="1">
        <stop offset="0" stop-color="#e9f3fa"/>
        <stop offset="1" stop-color="#bcd9ec"/>
      </linearGradient>
      <linearGradient id="beachTone" x1="0" y1="0" x2="0" y2="1">
        <stop offset="0" stop-color="#d7e9f5"/>
        <stop offset="0.55" stop-color="#a9cfe8"/>
        <stop offset="1" stop-color="#c9dde6"/>
      </linearGradient>
      <linearGradient id="lawnTone" x1="0" y1="0" x2="0" y2="1">
        <stop offset="0" stop-color="#9fc6e3"/>
        <stop offset="0.4" stop-color="#a8b98a"/>
        <stop offset="1" stop-color="var(--photo-grass)"/>
      </linearGradient>
    </defs>

    <!-- trim and fold marks -->
    <g stroke="var(--trim)" stroke-width="0.6">
      <line x1="55" y1="0" x2="55" y2="38"/><line x1="343" y1="0" x2="343" y2="38"/>
      <line x1="623" y1="0" x2="623" y2="38"/><line x1="913" y1="0" x2="913" y2="38"/>
      <line x1="55" y1="689" x2="55" y2="727"/><line x1="343" y1="689" x2="343" y2="727"/>
      <line x1="623" y1="689" x2="623" y2="727"/><line x1="913" y1="689" x2="913" y2="727"/>
      <line x1="0" y1="55" x2="36" y2="55"/><line x1="932" y1="55" x2="968" y2="55"/>
      <line x1="0" y1="667" x2="36" y2="667"/><line x1="932" y1="667" x2="968" y2="667"/>
    </g>

    <!-- paper -->
    <rect x="55" y="55" width="858" height="612" fill="url(#paperTint)"/>

    <!-- top middle photo -->
    <path d="M343 55H623V168C540 120 430 130 343 170Z" fill="url(#skyTone)" role="img" aria-label="Photo: woman holding a balancing yoga pose against a clear sky"/>
    <path d="M343 170C430 130 540 120 623 168V180C540 134 430 144 343 182Z" fill="var(--green)"/>

    <!-- left boat photo -->
    <path d="M55 192C150 210 260 172 343 170V182C260 186 150 226 55 216Z" fill="var(--green)"/>
    <path d="M55 216C150 226 260 186 343 182V470C280 450 170 470 55 440Z" fill="url(#seaTone)" role="img" aria-label="Photo: smiling senior couple sitting on the bow of a sailing yacht at sea"/>
    <path d="M55 440C170 470 280 450 343 470V488C270 468 170 490 55 462Z" fill="var(--paper)"/>
    <path d="M55 462C170 490 270 468 343 488V500C270 480 170 505 55 478Z" fill="var(--blue)"/>
    <circle cx="270" cy="467" r="40" fill="var(--paper)" stroke="#dfe9f1" stroke-width="1"/>

    <!-- right beach photo -->
    <path d="M623 272C720 290 830 300 913 322V334C830 312 720 302 623 284Z" fill="var(--blue)"/>
    <path d="M623 284C720 302 830 312 913 334V448C820 466 720 500 623 516Z" fill="url(#beachTone)" role="img" aria-label="Photo: man and woman practising tree pose on a beach"/>
    <path d="M623 516C720 500 820 466 913 448V460C820 478 720 512 623 528Z" fill="var(--green)"/>
    <path d="M623 528C720 512 820 478 913 460V470C820 490 720 522 623 536Z" fill="var(--blue)"/>

    <!-- bottom middle photo -->
    <path d="M343 482C430 468 540 466 623 478V667H343Z" fill="url(#lawnTone)" role="img" aria-label="Photo: group sitting cross-legged on mats meditating outdoors by the water"/>
  </svg>

  <div class="block questions">
    <ul class="ticks">
      <li>Are you looking at making changes this year?</li>
      <li>Are you stuck in a rut or at a crossroad in your life?</li>
      <li>Are you wanting to lose weigh but can’t get motivated?</li>
      <li>Do you have ongoing problems with your career, relationships, or just life itself?</li>
    </ul>
  </div>
  <div class="block answer">Life coaching is the answer!</div>

  <div class="block services justify">
    <h2>Life Coaching</h2>
    <p>Your Life Coach will give you the confidence and the ability to move forward in a positive manner in all areas of your life where you crave change. Life Coaching is about breaking down the barriers preventing this change from happening, and creating the ideal environment for positive action to take place. It is a holistic approach, which looks at the present and sets goals for a totally successful future.</p>
    <h2>Career Coaching</h2>
    <p>Are you at a crossroads in your career and at a loss about what to do next? Do you want your work to be in alignment with the authentic you? It can be difficult to assess career options, goals, and strategies, and have the confidence to implement changes on your own. With the right coaching support, you will gain the clarity that you need to take control and have a fulfilling and rewarding career.</p>
    <h2>Wellness Coaching</h2>
    <p>Health and wellness coaches help their clients find the motivation and tools to achieve their health and wellness goals, working with the client to examine and improve the psychological framework that supports those goals.</p>
  </div>

  <div class="block why">
    <h2>Why Would I Need Help?</h2>
    <p>Coaching is for anyone who wants to make lasting changes in their life.</p>
    <p>Coaching can assist with such issues as:</p>
    <ul class="ticks">
      <li>Creating a better work - life balance</li>
      <li>Resolving relationship issues</li>
      <li>Career guidance</li>
      <li>Stress management</li>
      <li>Weight loss and fitness</li>
      <li>Motivation and goal setting</li>
      <li>Boosting your self esteem</li>
      <li>Overcoming negative emotions and thoughts</li>
      <li>Better time management</li>
    </ul>
  </div>

  <div class="brand">Serene<br>Path</div>

  <div class="block about">
    <h2>Life Coaching and Meditation<br>Centre of Excellence</h2>
    <p>Our mission is to help you become the best possible person you can be. Mentally, physically, and spiritually. We offer highly qualified and compassionate trainers/coaches for Life Coaching, Meditation, Yoga and Pilates.</p>
    <p>They will guide and motivate you every step of the way to achieve all your dreams and goals. They will make you be the best you can be!</p>
  </div>

  <div class="block practice justify">
    <h2>Meditation</h2>
    <p>We specialise in teaching meditation from beginners to advanced and teach a variety of techniques for stress reduction, peace of mind, stillness, and clarity.</p>
    <h2>Yoga/Pilates</h2>
    <p>Your highly qualified and experienced Yoga or Pilates instructor will come to you and create a fun and varied workout based on what you enjoy and what your goals are.</p>
  </div>
</div>
</body>
</html>
```